Business Card Design

Hi I need a business card designed, we already have the business name logo artwork and would like some concept ideas for the Bus Card layout.
On the back of the card i want to include the products and services that we offer.
We are a Plastics Sheeting manufacture based in Perth Australia.

                                       

We need a BC design for a company called Tarvo Plastics based in Perth Australia.

We supply from DIY to Trade & Industrial  Engineering Markets.

We specialise in:

·         Cut to size panels  (all shapes and sizes)

·         Plastics fabrication & Welding

·         Custom Designs

·         Plastic Repairs

·         PVC Pipe Slotting & PVC Pipe Threading

·         Supplier of all types of engineering plastics and profiles.

Including:           Acrylic / Clarvene

                               Polycarbonate / Dorvil

                               Prismatic Light Diffuser

                               Vantrib

                               HDPE / UHMWPE

                               PVC / PVC Foam

                               Nylon

                               HIPS

```html
<!DOCTYPE html>
<html lang="en">
<head>
<meta charset="utf-8">
<title>Tarvo Plastics – Business Card</title>
<link rel="stylesheet" href="https://fonts.googleapis.com/css2?family=Source+Sans+3:ital,wght@0,400;0,600;0,700;1,700&display=swap">
<style>
  :root {
    --navy: #1f2a5a;
    --ink: #1c1c1c;
    --accent: #e07b24;
    --bullet: #2389c9;
    --card: #ffffff;
    --backdrop: #e9e6e1;
  }
  * { margin: 0; padding: 0; box-sizing: border-box; }
  html, body {
    width: 1200px; height: 963px; overflow: hidden;
    background: var(--backdrop);
    font-family: "Source Sans 3", Arial, sans-serif;
    color: var(--ink);
  }
  .canvas { position: relative; width: 1200px; height: 963px; }
  .card {
    position: absolute; background: var(--card);
    box-shadow: 0 2px 6px rgba(0,0,0,0.18);
    overflow: hidden;
  }
  .card--front { left: 79px; top: 36px; width: 487px; height: 866px; }
  .card--back { left: 640px; top: 53px; width: 493px; height: 862px; }
  .line {
    position: absolute; left: 0; right: 0; text-align: center;
    line-height: 1; white-space: nowrap;
  }
  .brand-name {
    top: 186px; font-size: 70px; font-weight: 700; color: var(--navy);
    letter-spacing: -1px;
  }
  .person { top: 518px; font-size: 28px; font-weight: 700; color: var(--navy); }
  .person .title { font-size: 22px; font-weight: 400; color: var(--accent); }
  .contact { font-size: 21px; display: flex; justify-content: center; align-items: center; gap: 6px; }
  .contact svg { width: 18px; height: 18px; fill: var(--ink); flex: none; }
  .contact--phone { top: 590px; }
  .contact--fax { top: 633px; }
  .contact--email { top: 672px; }
  .address { font-size: 21px; }
  .address--street { top: 738px; }
  .address--po { top: 771px; }
  .legal { top: 826px; font-size: 21px; }

  .intro { font-size: 24px; font-weight: 700; font-style: italic; color: var(--navy); }
  .heading { font-size: 30px; font-weight: 600; color: var(--navy); }
  .item { font-size: 21px; }
  .item .dot { color: var(--bullet); margin-right: 4px; }
</style>
</head>
<body>
<main class="canvas">
  <section class="card card--front" aria-label="Card front">
    <div class="line brand-name">Tarvo Plastics</div>
    <div class="line person">Your Name, <span class="title">Title</span></div>
    <div class="line contact contact--phone">
      <svg viewBox="0 0 24 24" aria-hidden="true"><path d="M6.6 10.8a15 15 0 0 0 6.6 6.6l2.2-2.2a1 1 0 0 1 1-.25 11.4 11.4 0 0 0 3.6.6 1 1 0 0 1 1 1V20a1 1 0 0 1-1 1A17 17 0 0 1 3 4a1 1 0 0 1 1-1h3.5a1 1 0 0 1 1 1 11.4 11.4 0 0 0 .6 3.6 1 1 0 0 1-.25 1z"/></svg>
      <span>08 5550 2011</span>
      <svg viewBox="0 0 24 24" aria-hidden="true"><path d="M8 1h8a2 2 0 0 1 2 2v18a2 2 0 0 1-2 2H8a2 2 0 0 1-2-2V3a2 2 0 0 1 2-2zm0 3v13h8V4z"/></svg>
      <span>0400 555 789</span>
    </div>
    <div class="line contact contact--fax">
      <svg viewBox="0 0 24 24" aria-hidden="true"><path d="M7 2h10v6H7zM4 9h16a2 2 0 0 1 2 2v7h-4v4H6v-4H2v-7a2 2 0 0 1 2-2zm4 8v3h8v-3z"/></svg>
      <span>08 5550 2022</span>
    </div>
    <div class="line contact contact--email">
      <svg viewBox="0 0 24 24" aria-hidden="true"><path d="M2 5h20v14H2zm2 2v.5l8 5 8-5V7zm0 3v7h16v-7l-8 5z"/></svg>
      <span>sales@tarvoplastics.com.au</span>
    </div>
    <div class="line address address--street">Unit 7/48 Merrin Circuit Alderwood WA 6021</div>
    <div class="line address address--po">PO Box 4821 Alderwood DC WA 6912</div>
    <div class="line legal">Kellow Holdings Pty Ltd T/A Tarvo Plastics ABN: TBA</div>
  </section>

  <section class="card card--back" aria-label="Card back">
    <div class="line intro" style="top:84px">The Products And Services</div>
    <div class="line intro" style="top:117px">That We Offer Are Supplied From</div>
    <div class="line intro" style="top:150px">Diy To Trade &amp; Industrial</div>
    <div class="line intro" style="top:183px">Engineering Markets</div>

    <div class="line heading" style="top:255px">We specialise in:</div>
    <div class="line item" style="top:298px"><span class="dot">•</span>Cut to size panels (all shapes and sizes)</div>
    <div class="line item" style="top:334px"><span class="dot">•</span>Plastics fabrication &amp; Welding</div>
    <div class="line item" style="top:372px"><span class="dot">•</span>Custom Designs <span class="dot">•</span>Plastic Repairs</div>
    <div class="line item" style="top:408px"><span class="dot">•</span>PVC Pipe Slotting &amp; PVC Pipe Threading</div>
    <div class="line item" style="top:444px"><span class="dot">•</span>Supplier of all types of engineering</div>
    <div class="line item" style="top:472px">plastics and profiles</div>

    <div class="line heading" style="top:554px">Including:</div>
    <div class="line item" style="top:601px"><span class="dot">•</span>Acrylic / Clarvene</div>
    <div class="line item" style="top:632px"><span class="dot">•</span>Polycarbonate / Dorvil</div>
    <div class="line item" style="top:662px"><span class="dot">•</span>Prismatic Light Diffuser</div>
    <div class="line item" style="top:694px">Vantrib &nbsp;<span class="dot">•</span> HDPE / UHMWPE</div>
    <div class="line item" style="top:725px"><span class="dot">•</span>PVC / PVC Foam</div>
    <div class="line item" style="top:755px"><span class="dot">•</span>Nylon &nbsp;<span class="dot">•</span> HIPS</div>
  </section>
</main>
</body>
</html>
```